Skin cancer clinic services trifold brochure

Need trifold brochure listing skin cancer services our clinic provides, staff information, location and brief about skin cancer with colours similar to our web site www.Tolvarin.clinic. I will provide more information regarding services and staff but want this colourful and standout as it will be given to other referring doctors or patients

Target Market(s)

Age 40 to 80 years

Industry/Entity Type

Medical

Font styles to use
Serif

Colors

Designer to choose colors to be used in the design.

Requirements
Must have
• Logo, services, contact info, beach or sun look and colours similar to web site or logo

```html
<!DOCTYPE html>
<html lang="en">
<head>
<meta charset="utf-8">
<title>Tolvarin Skin Clinic – Trifold Brochure</title>
<link rel="stylesheet" href="https://fonts.googleapis.com/css2?family=Crimson+Pro:wght@400;600&family=Libre+Baskerville:wght@400;700&family=Great+Vibes&display=swap">
<style>
  :root{
    --page-bg:#e9e9ea;
    --cream-top:#f8e9d8;
    --cream-bottom:#fdf4ea;
    --orange:#e2702a;
    --orange-deep:#c7531a;
    --amber:#eba722;
    --amber-deep:#d8841a;
    --ink:#2a1a12;
    --body-ink:#3a2c24;
    --white:#fffaf4;
    --cover-top:#e6a88c;
    --cover-mid:#c99186;
    --cover-bottom:#4a5163;
  }
  *{box-sizing:border-box;margin:0;padding:0}
  html,body{width:1200px;height:800px;overflow:hidden;background:var(--page-bg)}
  .brochure{position:absolute;left:79px;top:0;width:1042px;height:800px;display:flex}
  .panel{position:relative;height:800px;overflow:hidden}

  /* Team panel */
  .panel--team{width:340px;background:linear-gradient(180deg,var(--cream-top),var(--cream-bottom));font-family:"Crimson Pro",serif;color:var(--body-ink)}
  .team-title{position:absolute;left:22px;top:25px;font-family:"Libre Baskerville",serif;font-size:21px;color:var(--orange)}
  .team-title-bar{position:absolute;left:140px;top:36px;width:200px;height:9px;background:var(--orange)}
  .team-photo-band{position:absolute;left:0;top:66px;width:340px;height:206px;background:var(--orange)}
  .team-photo{position:absolute;left:0;top:76px;width:340px;height:186px;background:linear-gradient(180deg,#dcdde0,#c9ccd0)}
  .member{position:absolute;left:22px;width:296px}
  .member--right{text-align:right}
  .member-name{display:inline-block;font-family:"Libre Baskerville",serif;font-weight:700;font-size:11.5px;color:var(--ink);padding-bottom:3px;border-bottom:2px solid var(--ink);margin-bottom:9px}
  .member-bio{font-size:11px;line-height:14px}
  .team-footer-block{position:absolute;left:22px;top:776px;width:114px;height:24px;background:var(--orange)}

  /* Intro panel */
  .panel--intro{width:351px;font-family:"Crimson Pro",serif;color:var(--ink);text-align:center;background:linear-gradient(90deg,var(--amber),var(--amber-deep))}
  .intro-top{position:absolute;left:0;top:0;width:351px;height:422px;background:linear-gradient(90deg,var(--orange),var(--orange-deep))}
  .intro-heading{position:absolute;left:0;top:42px;width:351px;font-family:"Libre Baskerville",serif;font-weight:700;font-size:25px;line-height:33px}
  .intro-text{position:absolute;left:46px;top:137px;width:259px;font-size:15px;line-height:19px}
  .intro-text p+p{margin-top:18px}
  .intro-frame{position:absolute;left:33px;top:313px;width:296px;height:300px;background:var(--amber)}
  .intro-photo{position:absolute;left:44px;top:324px;width:274px;height:272px;background:linear-gradient(180deg,#6f8ca3,#3c3a40)}
  .contact-title{position:absolute;left:0;top:632px;width:351px;font-size:21px;font-weight:400}
  .contact-address{position:absolute;left:0;top:668px;width:351px;font-size:15px;line-height:16px}
  .contact-phone{position:absolute;left:0;top:710px;width:351px;font-size:21px;letter-spacing:.5px}
  .contact-email{position:absolute;left:0;top:746px;width:351px;font-size:15px}

  /* Cover panel */
  .panel--cover{width:351px}
  .cover-photo{position:absolute;inset:0;background:linear-gradient(180deg,var(--cover-top) 0%,var(--cover-mid) 50%,var(--cover-bottom) 100%)}
  .brand-name{position:absolute;right:24px;top:204px;font-family:"Crimson Pro",serif;font-weight:600;font-size:44px;color:var(--white)}
  .tagline{position:absolute;right:22px;top:580px;font-family:"Great Vibes",cursive;font-size:44px;line-height:46px;color:var(--white);text-align:right}
</style>
</head>
<body>
<main class="brochure">

  <section class="panel panel--team">
    <h2 class="team-title">Our Team</h2>
    <div class="team-title-bar"></div>
    <div class="team-photo-band"></div>
    <div class="team-photo" role="img" aria-label="Photo of a clinician in a lab coat and mask examining a sample"></div>

    <article class="member" style="top:288px">
      <h3 class="member-name">Dr. Maren Castell</h3>
      <p class="member-bio">BMed. FRACGP. Diploma Skin Cancer Medicine/Surgery. Diploma Aesthetic Medicine. Born in the USA. Maren gained her medical degree at Harbourview University. Dr. Castell enjoys the Outdoors, Gardening, Family, Boating, and Holidays. Professional interests include Skin Care, Cosmetic Treatments.</p>
    </article>

    <article class="member member--right" style="top:399px">
      <h3 class="member-name">Dr. Petra Lindqvist</h3>
      <p class="member-bio">BMed. FRACGP. Diploma Skin Cancer Medicine/Surgery. Born in Australia. Dr. Lindqvist enjoys the Outdoors, Gardening, Family, Beach, and Holidays. Professional interests include Skin Care &amp; Cosmetic Treatments, Family Medicine.</p>
    </article>

    <article class="member" style="top:492px">
      <h3 class="member-name">Dr. Helena Whitcombe</h3>
      <p class="member-bio">MBBS. Born in the USA and moved to Australia in 2004, Helena completed her Medical Degree at Coastline University. NSW. In 2004. Dr. Whitcombe enjoys Running, Fitness, Spending quality time with family and visiting the beach. Professional interests include Skin Care, Cosmetic Treatments and Family Medicine.</p>
    </article>

    <article class="member member--right" style="top:609px">
      <h3 class="member-name">Sorcha Dunleavy</h3>
      <p class="member-bio">Registered Nurse: ACNEM Certificate in Nutritional and Environmental Medicine<br>Medi Cosmetic Nurse: Sorcha is our Cosmetic Specialist and is available by appointment.</p>
    </article>

    <article class="member" style="top:699px">
      <h3 class="member-name">Ivy Thornbury</h3>
      <p class="member-bio">Registered Nurse: Ivy is our Laser Treatment Specialist and is available via appointment</p>
    </article>

    <div class="team-footer-block"></div>
  </section>

  <section class="panel panel--intro">
    <div class="intro-top"></div>
    <h1 class="intro-heading">When was your<br>last check?</h1>
    <div class="intro-text">
      <p>Tolvarin is a leading coastal skin cancer clinic based in Port Wendale.</p>
      <p>Headed by qualified professional Dr Maren Castell, Tolvarin engages the latest technology and clinical care to identify the best treatments and preventative measures for clients.</p>
    </div>
    <div class="intro-frame"></div>
    <div class="intro-photo" role="img" aria-label="Photo of a woman in a swimsuit seen from behind, looking out over a coastal bay"></div>
    <h2 class="contact-title">Contact Us</h2>
    <p class="contact-address">Suites 3 &amp; 4 217 Seaview Parade<br>Port Wendale NSW 2391</p>
    <p class="contact-phone">1300 586 174</p>
    <p class="contact-email">admin@tolvarin.clinic</p>
  </section>

  <section class="panel panel--cover">
    <div class="cover-photo" role="img" aria-label="Photo of a sunset over a calm beach"></div>
    <p class="brand-name">Tolvarin</p>
    <p class="tagline">Comfort<br>in your skin</p>
  </section>

</main>
</body>
</html>
```